Law Firm Header Revision

Task: Redesign my law firm Word document header (modern, succinct, logo-first, easy address updates)

I need you to revise and modernize my Microsoft Word document header for Law Office of Bram Holcott, PLLC. The result should look professional and clean on letters (including Letters of Protection), with the logo as the main focus and the text kept succinct.

Goals:
1. Create a modern, minimal header that feels premium and uncluttered.
Make the logo the most visually dominant element.
Reduce the visual weight of the contact/address block so it doesn’t distract from the document.
Make the address easy to change later (I’m moving offices soon) while keeping the same header design.

2. Content to include (keep all info accurate):
Law Office of Bram Holcott, PLLC
615 Pemberly St. Ste #300-214, Houston, TX 77002
Office: 832.555.0143
Direct: 713.555.0187
Fax: 832.555.0129
Bholcottlaw.com

3. Layout requirements:
Provide 3 header style options:
Logo left + contact info right
Centered logo + single concise contact line below
Logo left + firm name prominent + minimal contact line
The primary line near the logo should be minimal (preferably website + main office phone).
The address should be easy to update in one place without redesigning the header. Prefer either:
Move the full address to the footer, or
Put the address in a single dedicated line/block so I can edit it once and keep the layout unchanged.
4. Build constraints:
Must be achievable using standard Microsoft Word tools only (header/footer, tables, alignment, fonts, spacing). No advanced graphics software.
Provide exact header text, plus step-by-step Word instructions for each option:
Font recommendations + sizes
Alignment
Spacing
Table setup (if used)
How to keep it consistent across pages

5. Deliverable:
For each of the 3 options, provide:
The exact header content (with line breaks)
Formatting specs (fonts, sizes, spacing)
Word build steps so I can recreate it reliably and keep the logo as the focal point.

```html
<!DOCTYPE html>
<html lang="en">
<head>
<meta charset="utf-8">
<title>Bram Holcott Law – Letterhead Options</title>
<link href="https://fonts.googleapis.com/css2?family=Josefin+Sans:wght@300;400;600&display=swap" rel="stylesheet">
<style>
  :root {
    --board: #a6a6a6;
    --paper: #ffffff;
    --navy: #14213a;
    --ink: #1c1f26;
    --muted: #8a8f98;
    --rule: #cfd1d4;
    --watermark: #e9eaec;
  }
  * { margin: 0; padding: 0; box-sizing: border-box; }
  html, body { width: 1200px; height: 520px; overflow: hidden; }
  body {
    background: var(--board);
    font-family: "Josefin Sans", sans-serif;
    color: var(--ink);
    position: relative;
  }
  .sheet {
    position: absolute;
    top: 23px;
    width: 366px;
    height: 473px;
    background: var(--paper);
  }
  .sheet--logo-left { left: 24px; }
  .sheet--centered { left: 416px; }
  .sheet--firm-name { left: 811px; }

  .abs { position: absolute; line-height: 1; white-space: nowrap; }

  /* brand mark */
  .brand { display: flex; align-items: center; gap: 5px; }
  .brand__square { width: 29px; height: 29px; background: var(--navy); }
  .brand__name {
    font-weight: 400;
    color: var(--navy);
    font-size: 15px;
    letter-spacing: 0.2px;
  }
  .brand--small .brand__square { width: 24px; height: 24px; }
  .brand--small .brand__name { font-size: 13.5px; }
  .brand--large .brand__square { width: 30px; height: 30px; }
  .brand--large .brand__name { font-size: 16px; }

  .rule { position: absolute; height: 1px; background: var(--rule); left: 9px; right: 10px; }

  .watermark {
    position: absolute;
    left: 70px; top: 130px;
    width: 223px; height: 212px;
    background: var(--watermark);
  }
  .sheet--centered .watermark { left: 71px; }

  .contact-right { text-align: right; right: 10px; font-size: 9.5px; font-weight: 400; line-height: 12.5px; }
  .contact-line { left: 0; right: 0; text-align: center; font-size: 7px; font-weight: 300; color: var(--muted); letter-spacing: 0.2px; }
  .contact-line span + span { margin-left: 5px; }

  .firm { font-size: 9px; font-weight: 600; letter-spacing: 0.3px; }
  .detail { font-size: 7px; font-weight: 400; letter-spacing: 0.1px; }
  .doc-title { font-size: 8.5px; font-weight: 600; letter-spacing: 0.3px; right: 9px; text-align: right; }
  .page-num { font-size: 7px; right: 9px; text-align: right; }
  .left { left: 9px; }
</style>
</head>
<body>

  <!-- Option 1: logo left, contact right -->
  <section class="sheet sheet--logo-left" aria-label="Option 1: logo left with contact right">
    <div class="abs brand left" style="top:9px;">
      <span class="brand__square"></span><span class="brand__name">Bram Holcott Law</span>
    </div>
    <div class="abs contact-right" style="top:12px;">Office: 832.555.0143<br>Bholcottlaw.com</div>
    <div class="rule" style="top:46px;"></div>

    <div class="watermark" aria-hidden="true"></div>

    <div class="rule" style="top:426px;"></div>
    <p class="abs firm left" style="top:434px;">Law Office of Bram Holcott, PLLC</p>
    <p class="abs detail left" style="top:448px;">615 Pemberly St. Ste #300-214, Houston, TX 77002</p>
    <p class="abs detail left" style="top:459px;">Direct: 713.555.0187 &nbsp;|&nbsp; Fax: 832.555.0129</p>
    <p class="abs doc-title" style="top:434px;">Letters of Protection</p>
    <p class="abs page-num" style="top:448px;">Page 01</p>
  </section>

  <!-- Option 2: centered logo, single contact line -->
  <section class="sheet sheet--centered" aria-label="Option 2: centered logo with single contact line">
    <div class="abs brand brand--small" style="top:7px; left:0; right:0; justify-content:center;">
      <span class="brand__square"></span><span class="brand__name">Bram Holcott Law</span>
    </div>
    <p class="abs contact-line" style="top:41px;"><span>Office: 832.555.0143</span><span>Bholcottlaw.com</span></p>
    <div class="rule" style="top:52px;"></div>

    <div class="watermark" aria-hidden="true"></div>

    <div class="rule" style="top:427px;"></div>
    <p class="abs firm left" style="top:433px;">Law Office of Bram Holcott, PLLC</p>
    <p class="abs detail left" style="top:447px;">615 Pemberly St. Ste #300-214, Houston, TX 77002</p>
    <p class="abs detail left" style="top:458px;">Direct: 713.555.0187 &nbsp;|&nbsp; Fax: 832.555.0129</p>
    <p class="abs doc-title" style="top:433px;">Letters of Protection</p>
    <p class="abs page-num" style="top:447px;">Page 01</p>
  </section>

  <!-- Option 3: logo left, firm name prominent -->
  <section class="sheet sheet--firm-name" aria-label="Option 3: logo left with firm name prominent">
    <div class="abs brand brand--large left" style="top:12px;">
      <span class="brand__square"></span><span class="brand__name">Bram Holcott Law</span>
    </div>
    <p class="abs firm" style="top:9px; right:9px;">Law Office of Bram Holcott, PLLC</p>
    <div class="abs contact-right" style="top:25px; right:9px;">Office: 832.555.0143<br>Bholcottlaw.com</div>
    <div class="rule" style="top:54px;"></div>

    <div class="watermark" aria-hidden="true"></div>

    <div class="rule" style="top:439px;"></div>
    <p class="abs detail left" style="top:448px;">615 Pemberly St. Ste #300-214, Houston, TX 77002</p>
    <p class="abs detail left" style="top:459px;">Direct: 713.555.0187 &nbsp;|&nbsp; Fax: 832.555.0129</p>
    <p class="abs doc-title" style="top:447px;">Letters of Protection</p>
    <p class="abs page-num" style="top:459px;">Page 01</p>
  </section>

</body>
</html>
```